The Velvet Magpie business card

I need a business card for my makeup artist business. I specialise in bridal, glamour, formal and special occasion makeup.
I am a mobile makeup artist who caters for every from nowra to sydney.
I do the following services:
Bridal makeup
airbrush makeup
special occasion
formals
hens nights/ girls night
makeup lesson
makeup for all ages from flower girl to Nanna of the bride!
photoshoot makeup
SPFX

I would like the card to portray a very professional sleek makeup business. I would also like another version of the card directed especially towards brides.

Please see my website to understand colours etc www.thevelvetmagpie-example.com

The Velvet Magpie
Professional Makeup Artist
Lorraine Kedby
0491802643
info@thevelvetmagpie-example.com
www.thevelvetmagpie-example.com
www.facebook.com/thevelvetmagpie

```html
<!DOCTYPE html>
<html lang="en">
<head>
<meta charset="utf-8">
<title>The Velvet Magpie – Business Card</title>
<link rel="stylesheet" href="https://fonts.googleapis.com/css2?family=Open+Sans:wght@300;400;600;700&family=Roboto+Condensed:wght@700&display=swap">
<style>
  :root {
    --pink: #e0218a;
    --pink-deep: #c0126a;
    --pink-soft: #f06ab0;
    --white: #ffffff;
    --grey: #4a4a4c;
    --grey-dark: #3a3a3c;
    --ink: #2b1a22;
    --stage: #ebe9ea;
    --photo-light: #d9c3b3;
    --photo-mid: #9a8a76;
    --photo-dark: #4c4236;
  }
  * { box-sizing: border-box; margin: 0; padding: 0; }
  html, body {
    width: 1200px; height: 913px; overflow: hidden;
    background: var(--stage);
    font-family: "Open Sans", Arial, sans-serif;
  }
  .card {
    position: absolute; left: 280px;
    width: 640px; height: 356px;
    overflow: hidden;
    box-shadow: 0 6px 18px rgba(0,0,0,0.18);
  }
  .card--front { top: 52px; }
  .card--back { top: 476px; }

  .front-art { position: absolute; inset: 0; }

  .brand {
    position: absolute; left: 30px; top: 152px;
    height: 40px; line-height: 40px;
    white-space: nowrap;
    color: var(--pink);
    font-weight: 600; font-size: 28px;
    letter-spacing: 3px; text-transform: uppercase;
    transform: rotate(-12.8deg); transform-origin: left bottom;
  }

  .identity { position: absolute; left: 40px; top: 226px; color: var(--white); }
  .identity__name { font-weight: 700; font-size: 25px; line-height: 1.1; }
  .identity__role {
    font-size: 15px; padding-bottom: 6px; width: 250px;
    border-bottom: 2px solid var(--white);
  }

  .contacts { position: absolute; left: 44px; top: 290px; list-style: none; color: var(--white); font-size: 13px; }
  .contacts li { display: flex; align-items: center; gap: 10px; height: 20px; }
  .contacts svg { width: 14px; height: 14px; fill: var(--white); }

  .social {
    position: absolute; right: 22px; bottom: 26px;
    display: flex; flex-direction: column; align-items: flex-end; gap: 36px;
    color: var(--white); font-size: 13px;
  }
  .social__mark { width: 14px; height: 14px; background: var(--pink); }

  .back-photo {
    position: absolute; left: 0; top: 0; width: 100%; height: 250px;
    background:
      radial-gradient(ellipse at 72% 30%, var(--photo-light) 0%, transparent 55%),
      linear-gradient(120deg, var(--photo-mid) 0%, var(--photo-dark) 55%, var(--photo-mid) 100%);
  }
  .services {
    position: absolute; left: 0; bottom: 0; width: 100%; height: 106px;
    padding: 12px 22px;
    background: linear-gradient(90deg, var(--pink-deep), var(--pink) 45%, var(--pink-soft));
    font-family: "Roboto Condensed", "Arial Narrow", sans-serif;
    font-weight: 700; font-size: 15px; line-height: 20px;
    color: var(--ink);
  }
</style>
</head>
<body>

<section class="card card--front">
  <svg class="front-art" viewBox="0 0 640 356" aria-hidden="true">
    <defs>
      <linearGradient id="pinkFill" x1="0" y1="0" x2="1" y2="1">
        <stop offset="0" stop-color="#ea3a98"/>
        <stop offset="1" stop-color="#c8146f"/>
      </linearGradient>
      <linearGradient id="greyFill" x1="0" y1="0" x2="0" y2="1">
        <stop offset="0" stop-color="#3a3a3c"/>
        <stop offset="1" stop-color="#565658"/>
      </linearGradient>
    </defs>
    <rect width="640" height="356" fill="url(#pinkFill)"/>
    <polygon points="0,0 470,0 470,108 0,215" fill="#ffffff"/>
    <polygon points="290,0 470,0 470,18" fill="#e0218a"/>
    <polygon points="476,0 640,0 640,356 440,356" fill="url(#greyFill)"/>
    <polygon points="466,0 478,0 442,356 430,356" fill="#e6e6e6"/>
  </svg>

  <div class="brand">The Velvet Magpie</div>

  <div class="identity">
    <div class="identity__name">Lorraine Kedby</div>
    <div class="identity__role">Professional Makeup Artist</div>
  </div>

  <ul class="contacts">
    <li>
      <svg viewBox="0 0 16 16"><path d="M2 5c0-2 2-3 6-3s6 1 6 3v1h-3V5H5v1H2zM4 7h8l2 7H2z"/></svg>
      0491802643
    </li>
    <li>
      <svg viewBox="0 0 16 16"><path d="M1 3h14v10H1zM2 4l6 5 6-5v1L8 10 2 5z" fill-rule="evenodd"/></svg>
      info@thevelvetmagpie-example.com
    </li>
    <li>
      <svg viewBox="0 0 16 16"><circle cx="8" cy="8" r="7"/><path d="M1 8h14M8 1c-3 3-3 11 0 14M8 1c3 3 3 11 0 14" stroke="#c8146f" stroke-width="1" fill="none"/></svg>
      www.thevelvetmagpie-example.com
    </li>
  </ul>

  <div class="social">
    <span class="social__mark"></span>
    <span class="social__handle">|thevelvetmagpie</span>
  </div>
</section>

<section class="card card--back">
  <div class="back-photo" role="img" aria-label="Photo of a makeup artist applying false lashes to a client"></div>
  <p class="services">
    • Bridal makeup • Airbrush makeup • Special occasion • Formals<br>
    • Hens nights/ Girls night • Makeup lesson • Makeup for all ages from flower<br>
    girl to Nanna of the bride! • Photoshoot makeup • SPFX
  </p>
</section>

</body>
</html>
```